Hi Performance Vehicle Import business needs a Business card

Velmaroute Is a Melbourne based company importing and complying Japanese,American and European vehicles. We are expanding our company to a bigger factory in hopes to also expand our client base.

currently on our business cards we are advertising for the following
-Japanese, American and European vehicle importers
-ADR Compliance
-Direct import solutions
-Vehicle sales
-General maintenance

What we would like, is for customers to understand what we specialize in and be able to communicate with them by just looking at our business card.

We also have attached our current logo and previous cards with look outdated at the moment.

Target Market(s)

We are specializing in special enthusiast vehicles and only target a niche market as Imports in Australia are not very popular so we need to get our massage to everyone whos out there interested in such vehicles. We currently import Korvane Talwyn Bzx's, Haruvane Zel, Brannick Wolvers, Velocci's , Pelt Vandrels, Tuvano's and Orvelli and Zendo's near future.We are targeting younger generation as well as mature crowd bit of everyone..

Industry/Entity Type

Advertising

Requirements
Must have
• Lets look at few designs and we will work with the designer once preferable design has been selected.
Nice to have
• We would like to see something in the back ground to represent the automotive field. Bring your creativity so we might change our mind. We still like to keep the existing logo.
Should not have
• The business cards attached are from our local designer. We think they are outdated,wrong fonts and arrangement of the information is not quite right. So we would like to see something totally different.

```html
<!DOCTYPE html>
<html lang="en">
<head>
<meta charset="utf-8">
<title>Velmaroute Business Card</title>
<link rel="stylesheet" href="https://fonts.googleapis.com/css2?family=Exo+2:wght@400;600&display=swap">
<style>
  :root{
    --bg:#e9e6e1;
    --card-black:#0b0b0c;
    --logo-panel:#1a1a1c;
    --red:#d4121b;
    --red-deep:#9c0a10;
    --grey:#a9a9ad;
    --white:#f4f4f4;
    --soft:#cfcfcf;
  }
  *{box-sizing:border-box;margin:0;padding:0}
  html,body{width:1200px;height:987px;overflow:hidden}
  body{background:var(--bg);font-family:"Exo 2",sans-serif;color:var(--white);position:relative}
  .card{position:absolute;top:161px;width:380px;height:665px;background:var(--card-black);overflow:hidden;box-shadow:0 10px 30px rgba(0,0,0,.25)}
  .card--back{left:170px}
  .card--front{left:650px}
  .card__shapes{position:absolute;inset:0;width:100%;height:100%}
  .logo-panel{position:absolute;left:0;right:0;height:78px;background:var(--logo-panel);display:flex;flex-direction:column;align-items:center;justify-content:center;gap:4px}
  .card--back .logo-panel{top:200px}
  .card--front .logo-panel{top:52px}
  .logo-name{font-weight:600;font-size:30px;letter-spacing:4px;color:var(--white);text-transform:uppercase}
  .logo-tagline{font-size:9px;letter-spacing:2px;color:var(--soft);text-transform:uppercase}
  .identity{position:absolute;top:200px;right:34px;text-align:right}
  .identity__name{font-weight:600;font-size:27px;letter-spacing:2px;text-transform:uppercase}
  .identity__role{font-size:15px;letter-spacing:3px;text-transform:uppercase;margin-top:2px}
  .contacts{position:absolute;top:300px;left:30px;right:20px;display:grid;grid-template-columns:1fr 1.35fr;row-gap:14px;column-gap:8px;font-size:12px;letter-spacing:.5px}
  .contact{display:flex;align-items:center;gap:7px;white-space:nowrap}
  .contact svg{width:16px;height:16px;flex:none}
  .address{position:absolute;top:545px;left:0;right:0;text-align:center;font-size:15px;letter-spacing:1px;line-height:1.45}
  .address svg{display:block;margin:0 auto 8px;width:30px;height:30px}
</style>
</head>
<body>

<section class="card card--back" aria-label="Card back">
  <svg class="card__shapes" viewBox="0 0 380 665" aria-hidden="true">
    <defs>
      <linearGradient id="redBack" x1="0" y1="0" x2="1" y2="1">
        <stop offset="0" stop-color="#ef1c25"/><stop offset="1" stop-color="#8e0a0f"/>
      </linearGradient>
    </defs>
    <polygon points="170,0 380,0 380,62 330,26" fill="url(#redBack)"/>
    <polygon points="0,450 190,520 380,450 380,466 190,536 0,466" fill="var(--grey)"/>
    <polygon points="0,466 190,536 380,466 380,665 0,665" fill="url(#redBack)"/>
  </svg>
  <div class="logo-panel">
    <span class="logo-name">Velmaroute</span>
    <span class="logo-tagline">Performance Vehicle Imports</span>
  </div>
</section>

<section class="card card--front" aria-label="Card front">
  <svg class="card__shapes" viewBox="0 0 380 665" aria-hidden="true">
    <defs>
      <linearGradient id="redFront" x1="0" y1="0" x2="1" y2="1">
        <stop offset="0" stop-color="#ef1c25"/><stop offset="1" stop-color="#8e0a0f"/>
      </linearGradient>
    </defs>
    <polygon points="170,0 380,0 380,62 330,26" fill="url(#redFront)"/>
    <polygon points="0,450 190,520 380,450 380,466 190,536 0,466" fill="var(--grey)"/>
    <polygon points="0,466 190,536 380,466 380,665 0,665" fill="url(#redFront)"/>
  </svg>

  <div class="logo-panel">
    <span class="logo-name">Velmaroute</span>
    <span class="logo-tagline">Performance Vehicle Imports</span>
  </div>

  <div class="identity">
    <h1 class="identity__name">Darren Kesh</h1>
    <p class="identity__role">General Manager</p>
  </div>

  <div class="contacts">
    <div class="contact">
      <svg viewBox="0 0 16 16" aria-hidden="true"><circle cx="8" cy="8" r="7" fill="none" stroke="#f4f4f4" stroke-width="1.2"/><path d="M5.5 4.5l1.5 0 .6 1.8-.9.7a5 5 0 0 0 2.3 2.3l.7-.9 1.8.6v1.5c-3.7.3-6.3-2.3-6-6z" fill="#f4f4f4"/></svg>
      <span>014 820 3371</span>
    </div>
    <div class="contact">
      <svg viewBox="0 0 16 16" aria-hidden="true"><circle cx="8" cy="8" r="7" fill="none" stroke="#f4f4f4" stroke-width="1.2"/><rect x="4" y="5.2" width="8" height="5.6" fill="none" stroke="#f4f4f4" stroke-width="1"/><path d="M4 5.4l4 3 4-3" fill="none" stroke="#f4f4f4" stroke-width="1"/></svg>
      <span>d.kesh@velmaroute.com</span>
    </div>
    <div class="contact">
      <svg viewBox="0 0 16 16" aria-hidden="true"><circle cx="8" cy="8" r="7" fill="none" stroke="#f4f4f4" stroke-width="1.2"/><path d="M5.5 4.5l1.5 0 .6 1.8-.9.7a5 5 0 0 0 2.3 2.3l.7-.9 1.8.6v1.5c-3.7.3-6.3-2.3-6-6z" fill="#f4f4f4"/></svg>
      <span>014 820 3371</span>
    </div>
    <div class="contact">
      <svg viewBox="0 0 16 16" aria-hidden="true"><circle cx="8" cy="8" r="7" fill="none" stroke="#f4f4f4" stroke-width="1.2"/><circle cx="8" cy="8" r="4" fill="none" stroke="#f4f4f4" stroke-width="1"/><path d="M4 8h8M8 4v8" stroke="#f4f4f4" stroke-width=".8"/></svg>
      <span>www.velmaroute.com.au</span>
    </div>
  </div>

  <address class="address" style="font-style:normal">
    <svg viewBox="0 0 30 30" aria-hidden="true"><circle cx="15" cy="15" r="14" fill="none" stroke="#f4f4f4" stroke-width="1.6"/><path d="M15 7a5 5 0 0 1 5 5c0 4-5 10-5 10s-5-6-5-10a5 5 0 0 1 5-5z" fill="#f4f4f4"/><circle cx="15" cy="12" r="1.8" fill="#c81018"/></svg>
    57 Larkin Road<br>2nd Floor, Unit W
  </address>
</section>

</body>
</html>
```